Dog grooming business card
This is a business card for m dog grooming business like it say above.
In the priorities box below I will have the text that I want on the card.

Industry/Entity Type

Business

Colors

Designer to choose colors to be used in the design.

Requirements
Must have
• My logo and the insurance stamp must be on the card.

Text it must have :

Professional grooming services
Email: lunabrisk@mailvale.net
Text or call 1 705 318 6052
TWF certified/member
Pet first aid certified
Next appointment ___________________________________
Nice to have
• Greens to match my logo

```html
<!DOCTYPE html>
<html lang="en">
<head>
<meta charset="utf-8">
<title>Luna Brisk – Business Card Front and Back</title>
<link rel="stylesheet" href="https://fonts.googleapis.com/css2?family=Cinzel:wght@400;600&family=Montserrat:wght@500&display=swap">
<style>
  :root {
    --backdrop-light: #e6e6e6;
    --backdrop-dark: #8a8a8a;
    --card-dark: #2b2b2b;
    --card-dark-facet: #3a3a3a;
    --card-light: #ffffff;
    --ink-light: #f2f2f2;
    --ink-muted: #bdbdbd;
    --ink-dark: #444444;
    --rule-light: #8c8c8c;
    --rule-dark: #a9a9a9;
    --badge-fill: #ececec;
    --badge-edge: #9a9a9a;
  }
  * { box-sizing: border-box; margin: 0; padding: 0; }
  html, body { width: 1200px; height: 1000px; overflow: hidden; }
  body {
    background: radial-gradient(ellipse at 50% 40%, var(--backdrop-light) 0%, #c9c9c9 55%, var(--backdrop-dark) 100%);
    font-family: "Montserrat", sans-serif;
    position: relative;
  }
  .card {
    position: absolute;
    top: 340px;
    width: 525px;
    height: 300px;
    box-shadow: 0 14px 30px rgba(0,0,0,0.28);
    overflow: hidden;
  }
  .card--front {
    left: 50px;
    background: linear-gradient(155deg, var(--card-dark-facet) 0%, var(--card-dark-facet) 42%, var(--card-dark) 42.2%, #242424 100%);
  }
  .card--back {
    left: 625px;
    background: var(--card-light);
  }
  .brand {
    position: absolute;
    display: flex;
    flex-direction: column;
    align-items: center;
    width: 200px;
  }
  .card--front .brand { left: 40px; top: 58px; }
  .card--back .brand { left: 162px; top: 52px; }
  .brand__mark {
    display: flex;
    align-items: center;
    gap: 8px;
    margin-bottom: 12px;
  }
  .brand__dot {
    width: 14px; height: 14px; border-radius: 50%;
  }
  .brand__name {
    font-family: "Cinzel", serif;
    font-weight: 600;
    font-size: 24px;
    letter-spacing: 1px;
  }
  .card--front .brand__dot { background: var(--ink-muted); }
  .card--front .brand__name { color: var(--ink-light); }
  .card--back .brand__dot { background: var(--ink-dark); }
  .card--back .brand__name { color: var(--ink-dark); }
  .brand__tagline {
    width: 170px;
    text-align: center;
    font-family: "Cinzel", serif;
    font-weight: 400;
    line-height: 1.15;
    padding: 8px 0 9px;
    border-top: 1px solid;
    border-bottom: 1px solid;
  }
  .brand__tagline span { display: block; }
  .brand__tagline .small { font-size: 13px; letter-spacing: 1.5px; }
  .brand__tagline .large { font-size: 18px; letter-spacing: 2px; }
  .card--front .brand__tagline { color: var(--ink-light); border-color: var(--rule-light); }
  .card--back .brand__tagline { color: var(--ink-dark); border-color: var(--rule-dark); }
  .contact-list {
    position: absolute;
    left: 285px;
    top: 92px;
    list-style: none;
    color: var(--ink-light);
    font-size: 11px;
    font-variant: small-caps;
    letter-spacing: 0.6px;
  }
  .contact-list li {
    display: flex;
    align-items: center;
    gap: 8px;
    height: 22px;
  }
  .contact-list .lead { font-weight: 500; }
  .contact-list svg { width: 12px; height: 12px; flex: none; }
  .insurance-badge {
    position: absolute;
    right: 26px;
    top: 20px;
    width: 86px;
    height: 54px;
    border-radius: 8px;
    background: var(--badge-fill);
    border: 1.5px solid var(--badge-edge);
  }
  .appointment {
    position: absolute;
    left: 70px;
    right: 70px;
    top: 238px;
    display: flex;
    align-items: flex-end;
    gap: 10px;
    color: var(--ink-dark);
    font-family: "Cinzel", serif;
    font-size: 13px;
    letter-spacing: 1px;
    white-space: nowrap;
  }
  .appointment__line {
    flex: 1;
    border-bottom: 1px solid var(--rule-dark);
    margin-bottom: 3px;
  }
</style>
</head>
<body>
  <section class="card card--front" aria-label="Card front">
    <div class="brand">
      <div class="brand__mark">
        <span class="brand__dot"></span>
        <span class="brand__name">Luna Brisk</span>
      </div>
      <div class="brand__tagline">
        <span class="small">Professional</span>
        <span class="large">Grooming</span>
        <span class="small">Services</span>
      </div>
    </div>
    <ul class="contact-list">
      <li class="lead">
        <svg viewBox="0 0 12 12"><circle cx="6" cy="6" r="4" fill="var(--ink-muted)"/></svg>
        Professional Grooming Services
      </li>
      <li>
        <svg viewBox="0 0 12 12"><rect x="1" y="2.5" width="10" height="7" fill="none" stroke="var(--ink-muted)" stroke-width="1.2"/><path d="M1 2.5 L6 6.5 L11 2.5" fill="none" stroke="var(--ink-muted)" stroke-width="1.2"/></svg>
        lunabrisk@mailvale.net
      </li>
      <li>
        <svg viewBox="0 0 12 12"><path d="M2.5 1.5 L4.5 1.5 L5.3 4 L4 5 Q5 7.5 7 8 L8 6.7 L10.5 7.5 L10.5 9.5 Q10.5 10.5 9.5 10.5 Q2 10 1.5 2.5 Q1.5 1.5 2.5 1.5 Z" fill="var(--ink-muted)"/></svg>
        1 705 318 6052
      </li>
      <li>
        <svg viewBox="0 0 12 12"><path d="M2 6.5 L5 9.5 L10.5 2.5" fill="none" stroke="var(--ink-muted)" stroke-width="1.6"/></svg>
        TWF Certified/Member
      </li>
      <li>
        <svg viewBox="0 0 12 12"><path d="M2 6.5 L5 9.5 L10.5 2.5" fill="none" stroke="var(--ink-muted)" stroke-width="1.6"/></svg>
        Pet First Aid Certified
      </li>
    </ul>
  </section>

  <section class="card card--back" aria-label="Card back">
    <div class="insurance-badge" role="img" aria-label="Insurance protection stamp"></div>
    <div class="brand">
      <div class="brand__mark">
        <span class="brand__dot"></span>
        <span class="brand__name">Luna Brisk</span>
      </div>
      <div class="brand__tagline">
        <span class="small">Professional</span>
        <span class="large">Grooming</span>
        <span class="small">Services</span>
      </div>
    </div>
    <p class="appointment">
      <span class="appointment__label">Next appointment</span>
      <span class="appointment__line"></span>
    </p>
  </section>
</body>
</html>
```